Bright Meadow Kitchen Business Cards

We need Business cards development for our expanding business. Our Company BrightMeadowKitchen promotes grain free living through products, services and healthy living concepts. Our Products are:
Non-Grain
Non- GMO
Non- Soy
Gluten-Free
Updates

Project Deadline Extended
Reason: We will need to extend the deadline on our Business Card contest. Thanks, BMK

Industry/Entity Type

Business

```html
<!DOCTYPE html>
<html lang="en">
<head>
<meta charset="utf-8">
<title>Bright Meadow Kitchen Business Card</title>
<link rel="stylesheet" href="https://fonts.googleapis.com/css2?family=Questrial&family=Michroma&display=swap">
<style>
  :root {
    --bg: #e6e6e6;
    --card: #ffffff;
    --green-dark: #1d7a35;
    --green-band: #16752f;
    --green-band-edge: #0f5c24;
    --green-light: #6cc24a;
    --green-icon: #5cb848;
    --text-dark: #1e5f2c;
  }
  * { margin: 0; padding: 0; box-sizing: border-box; }
  html, body { width: 1200px; height: 900px; overflow: hidden; }
  body {
    background: radial-gradient(ellipse at center, #f2f2f2 0%, var(--bg) 75%);
    font-family: "Questrial", sans-serif;
  }
  .card {
    position: absolute;
    left: 160px; top: 170px;
    width: 880px; height: 560px;
    background: var(--card);
    border-radius: 40px;
    box-shadow: 0 18px 40px rgba(0,0,0,0.18);
  }
  .brand {
    position: absolute;
    left: 60px; top: 68px;
    display: inline-block;
  }
  .brand-line { display: flex; align-items: flex-end; gap: 8px; }
  .brand-name {
    font-size: 54px; line-height: 1; letter-spacing: -1px;
    color: var(--green-dark);
  }
  .brand-suffix {
    font-size: 14px; color: var(--green-light);
    padding-bottom: 4px;
  }
  .tagline {
    margin-top: 8px;
    font-size: 19px; letter-spacing: 1.5px; color: var(--green-light);
    text-align: right; padding-right: 40px;
  }
  .product-band {
    position: absolute; left: 0; right: 0; top: 232px; height: 30px;
    background: linear-gradient(180deg, var(--green-band) 0%, var(--green-band-edge) 100%);
    display: flex; justify-content: space-around; align-items: center;
    padding: 0 30px;
  }
  .product-band span {
    font-family: "Michroma", sans-serif;
    font-size: 15px; letter-spacing: 2px; color: #fff;
    font-variant: small-caps;
  }
  .person { position: absolute; left: 60px; top: 298px; }
  .person-name { font-size: 36px; color: var(--green-dark); -webkit-text-stroke: 0.6px var(--green-dark); }
  .person-role { font-size: 23px; color: var(--green-light); margin-top: 4px; }
  .contact { position: absolute; left: 60px; top: 398px; list-style: none; }
  .contact li {
    display: flex; align-items: center; gap: 16px;
    font-size: 27px; color: var(--text-dark); height: 36px;
  }
  .contact svg { width: 26px; height: 26px; fill: var(--green-icon); flex: none; }
</style>
</head>
<body>
  <div class="card">
    <div class="brand">
      <div class="brand-line">
        <div class="brand-name">BrightMeadowKitchen</div>
        <div class="brand-suffix">LLC</div>
      </div>
      <div class="tagline">Simple Meals For Brighter Days</div>
    </div>

    <div class="product-band">
      <span>Non-Grain</span>
      <span>Non- GMO</span>
      <span>Non- Soy</span>
      <span>Gluten-Free</span>
    </div>

    <div class="person">
      <div class="person-name">Dana Whitlow</div>
      <div class="person-role">Manager</div>
    </div>

    <ul class="contact">
      <li>
        <svg viewBox="0 0 24 24" aria-hidden="true"><path d="M6.6 10.8a15.1 15.1 0 0 0 6.6 6.6l2.2-2.2c.3-.3.7-.4 1-.2 1.1.4 2.3.6 3.6.6.6 0 1 .4 1 1V20c0 .6-.4 1-1 1A17 17 0 0 1 3 4c0-.6.4-1 1-1h3.5c.6 0 1 .4 1 1 0 1.3.2 2.5.6 3.6.1.3 0 .7-.2 1z"/></svg>
        1584 321 460
      </li>
      <li>
        <svg viewBox="0 0 24 24" aria-hidden="true"><path d="M12 3 2 12h3v8h5v-5h4v5h5v-8h3z"/></svg>
        PO Box 40517 AL 36602
      </li>
      <li>
        <svg viewBox="0 0 24 24" aria-hidden="true"><path d="M3 6h18v12H3z" fill="none" stroke="#5cb848" stroke-width="2"/><path d="M3 6l9 7 9-7" fill="none" stroke="#5cb848" stroke-width="2"/></svg>
        info@brightmeadowkitchen.com
      </li>
      <li>
        <svg viewBox="0 0 24 24" aria-hidden="true"><g fill="none" stroke="#5cb848" stroke-width="1.8"><circle cx="12" cy="12" r="9"/><ellipse cx="12" cy="12" rx="4" ry="9"/><path d="M3 12h18M5 7h14M5 17h14"/></g></svg>
        www.brightmeadowkitchen.com
      </li>
    </ul>
  </div>
</body>
</html>
```